Bold, Modern, Clean "Kestrelwaymassage.com" website

Why we stand out?
We are a male and female mobile massage team. Our names are Paul and Lina. 
Kestrel Way is a Seattle based mobile massage service. Our massage is offered to the community with a goal of facilitating balance within each individual. We specialize in integrated Pain management, and sports/medical massage therapy. Every client's first assessment is attended by our male and female massage therapist team. Depending on the goals identified for an individual determines which therapist will be assigned to provide treatment, if not both.

Our passion...
Here at Kestrel Way, we have a great passion for Postural Resoration and how it is integrated into an individual's Massage treatment. We pride ourselves in being natural facilitators of healing, which takes the ego of the therapist out of the client's healing process. We strive to deliver the best massage possible by including modalities such as Neuromuscular, Myofascial release, spontaneous muscle release, postural restoration, orthopedic, and medical massage.

Our education...

We are both Graduates of Venmora, school of massage therapy. We have continuing education in medical massage, myofacial release, trigger point therapy, postural restoration, anatomy, and spontaneous muscle release. Lina is also a Certified Yoga Instructor, which amplifies her experience with flexibility and strength as it pertains to each individual. Paul's passion is Massage, stretching, and strength training to encourage postural restoration and realignment.

Our rates-

Our rates are $75/ 60 minutes, $95/ 90 minutes, and $120/ 120 minutes.

Education-
Both Lina and I worked as behavioral health professionals that specialized in life skills mentoring for youth who had experienced different types of trauma. This led us both to want to help others in a different environment, where individuals can be empowered to take responsibility over their own healing. To us, massage is a type of manipulation physical therapy, that encourages healing on many levels.

Advice to any massage client-
The most important thing to 'us', as Licenced providers is to get you on to our table to show you our skills. But a good therapist never forgets that it's not about what we do for you, but what we can facilitate for you. Your health and healing has nothing to do with us. It is yours, not ours. Identify what your goals are with any Therapist, and know what the end looks like. Progress should be tangible, such as range of motion, and decreased pain.

Lina and Paul at Kestrel Way are awesome! I recently had open heart surgery, and Lina worked on me to increase my range of motion while helping with the pinched nerve from my arm being in the same position for so long during my surgery. My wife drives a lot for work, and Paul has helped decrease her neck and lower back pain immensely. They are seriously the best therapists I have ever worked with. I would recommend them to anyone who needs anything from stress relief to a medical massage treatment. They are professional, up beat, easy going, and always on time. And, I love that they meet us where ever we like! We did a staycation recently, where they came to our hotel to give us relaxation massages. Although usually they come to our home, where we focus on pain related issues. We will continue to work with them for a long, long time.

Target Market(s)

Mobile massage therapy clients

Industry/Entity Type

Massage Therapy

Coding

Coded - Design and coding required

Number of Pages Required

1 page

Font styles to use
Serif
Sans Serif

Requirements
Must have
• Please add or remove any information that would help the presentation of our website. Our logo is posted below, please include into the website.
• Please include a contact field that includes, kestrelwaymassage@fernmail.net,
• (206) 555-0148
• We have also included our own stock photos, as well as a photo of Paul and Lina. Please include a cropped photo of both massage therapists.

```html
<!DOCTYPE html>
<html lang="en">
<head>
<meta charset="utf-8">
<title>Kestrel Way – Mobile Massage</title>
<link rel="stylesheet" href="https://fonts.googleapis.com/css2?family=Lato:wght@400;700&family=Arvo:wght@700&family=Marck+Script&family=Alegreya:wght@700&family=Signika:wght@400&display=swap">
<style>
:root{
  --red:#c1504d;
  --red-dark:#a8403d;
  --red-light:#d66b68;
  --navy:#1c1aa0;
  --footer:#28235f;
  --orange:#e8923a;
  --grey-text:#8a8a8a;
  --body-text:#3a3a3a;
  --panel:#f2f2f2;
  --line:#d9b2a4;
  --blue-btn:#1436b8;
}
*{box-sizing:border-box;margin:0;padding:0}
html,body{width:1200px;height:2406px;overflow:hidden}
body{position:relative;background:#fff;font-family:"Lato",sans-serif;color:var(--body-text)}
.abs{position:absolute}

/* top bar */
.quick-btn{left:82px;top:18px;width:151px;height:35px;border-radius:18px;background:var(--blue-btn);color:#fff;font:700 13px "Lato",sans-serif;display:flex;align-items:center;justify-content:center;gap:7px}
.top-contact{top:22px;font-size:14px;color:#333;display:flex;align-items:center;gap:8px}
.nav-band{left:0;top:72px;width:1200px;height:56px;background:var(--red);border-top:1px dashed rgba(255,255,255,.5);border-bottom:1px dashed rgba(255,255,255,.5);box-shadow:inset 0 4px 0 var(--red-dark),inset 0 -4px 0 var(--red-dark)}
.nav-item{top:90px;font-size:14.5px;color:#fff;letter-spacing:.5px;text-transform:uppercase}
.nav-item.active{color:#f6c08f}
.nav-star{top:89px;color:#fff;font-size:13px}
.logo-disc{left:528px;top:28px;width:144px;height:144px;border-radius:50%;background:#1d3cc0;border:4px solid #fff;box-shadow:0 0 0 2px #1d3cc0;display:flex;flex-direction:column;align-items:center;justify-content:center;color:#fff;font:700 22px/1.05 "Lato",sans-serif;text-align:center}

/* hero */
.hero{left:0;top:128px;width:1200px;height:533px;background:linear-gradient(90deg,#d9c7a6 0%,#f4efe5 25%,#fbf7f1 45%,#e9cdb6 65%,#d8a98a 85%,#efe2d4 100%)}
.hero-title{left:288px;top:198px;font:62px/1 "Marck Script",cursive;color:var(--red)}
.hero-sub{left:305px;top:272px;font:700 64px/1 "Alegreya",serif;color:var(--orange);letter-spacing:1px}
.hero-tag{left:358px;top:344px;font-size:28px;color:#222}

/* sections */
.section-title{left:0;width:1200px;text-align:center;font:700 30px "Arvo",serif;color:var(--red);letter-spacing:.5px}
.section-title span{color:var(--navy)}
.divider{left:500px;width:200px;height:20px}
.about-lead{left:80px;top:778px;width:1038px;text-align:center;font-size:12.5px;line-height:21px;color:#333}
.about-photo{left:56px;top:866px;width:497px;height:313px;background:radial-gradient(ellipse at 40% 55%,#d9567a 0%,#e993a8 30%,#f7e6ea 60%,#fff 80%)}
.feature-icon{width:84px;height:84px;border-radius:50%;background:var(--red);border:5px solid #fff;box-shadow:0 0 0 2px #e3c6c2;display:flex;align-items:center;justify-content:center}
.feature-title{left:717px;font:700 17px "Lato",sans-serif;color:var(--red)}
.feature-text{left:718px;width:392px;font-size:12.5px;line-height:20px;color:var(--grey-text)}
.read-more{left:1037px;font:700 11.5px "Lato",sans-serif;color:var(--navy);text-decoration:underline;display:flex;align-items:center;gap:6px}

.prices{left:0;top:1184px;width:1200px;height:532px;background:var(--panel);border-top:2px solid #dcdcdc;border-bottom:2px solid #dcdcdc}
.price-card{top:1318px;width:241px;height:355px;background:#fff;border:1px solid #c9c9c9;padding:5px}
.price-card .head{height:129px;background:linear-gradient(#c85653,#b94643);color:#fff;text-align:center;font:29px "Signika",sans-serif;padding-top:18px}
.price-card .badge{position:absolute;left:62px;top:76px;width:117px;height:117px;border-radius:50%;background:#fff;border:3px solid #eee;display:flex;align-items:center;justify-content:center;font:700 36px "Lato",sans-serif;color:var(--navy)}
.price-card .name{position:absolute;left:0;top:203px;width:100%;text-align:center;font:20px "Lato",sans-serif;color:var(--navy);text-transform:uppercase}
.price-card .desc{position:absolute;left:14px;top:232px;width:211px;text-align:center;font-size:12.5px;line-height:16px;color:#555}
.price-card .btn{position:absolute;left:67px;top:295px;width:107px;height:33px;background:var(--red);color:#fff;font-size:13.5px;display:flex;align-items:center;justify-content:center}

.avatar{left:547px;top:1853px;width:106px;height:106px;border-radius:50%;border:2px dashed #b9b9b9;padding:6px}
.avatar div{width:100%;height:100%;border-radius:50%;background:linear-gradient(#dfe5ea,#9aa6b2)}
.quote-mark{left:258px;top:1960px;font:700 48px "Alegreya",serif;color:#f1d9d6}
.quote-text{left:280px;top:1978px;width:640px;text-align:center;font-size:12.8px;line-height:22px;color:#333}
.quote-name{left:0;top:2025px;width:1200px;text-align:center;font:700 12.8px "Lato",sans-serif;color:#222}
.dot{top:2066px;width:12px;height:12px;border-radius:50%;background:var(--red)}
.dot.on{background:var(--navy)}
.spa-left{left:0;top:1997px;width:257px;height:117px;background:radial-gradient(ellipse at 40% 70%,#8e7aa8 0%,#b8aac6 35%,rgba(255,255,255,0) 75%)}
.spa-right{left:898px;top:1909px;width:302px;height:205px;background:radial-gradient(ellipse at 70% 45%,#f4f4f4 0%,#e4e4e4 35%,rgba(255,255,255,0) 75%),radial-gradient(ellipse at 25% 80%,#c7dc7a 0%,rgba(255,255,255,0) 40%)}

/* footer */
.footer{left:0;top:2114px;width:1200px;height:257px;background:var(--footer)}
.footer-title{top:2150px;font-size:17px;color:#fff}
.footer-rule{top:2182px;height:0;border-top:1px dashed rgba(255,255,255,.45)}
.footer-sep{top:2150px;width:0;height:190px;border-left:1px solid rgba(255,255,255,.2)}
.quick-links{left:82px;top:2194px;list-style:none;font-size:12.8px;line-height:24px;color:#fff}
.quick-links li::before{content:"›";margin-right:10px;color:#cfcfe8}
.field{left:311px;width:226px;background:#fff;border-radius:3px;font-size:12.5px;color:#333;padding:4px 8px}
.submit{left:311px;top:2307px;width:64px;height:22px;background:#d06a68;color:#fff;font-size:12.5px;display:flex;align-items:center;justify-content:center;border-radius:2px}
.contact-row{left:642px;width:240px;font-size:12.8px;line-height:19px;color:#fff;display:flex;gap:10px}
.footer-logo{left:983px;top:2154px;width:128px;height:128px;border-radius:50%;background:#3e3a7e;border:3px solid #6d69a3;display:flex;flex-direction:column;align-items:center;justify-content:center;color:#c9c8e6;font:700 19px/1.1 "Lato",sans-serif;text-align:center}
.social{top:2300px;width:32px;height:32px;border-radius:50%}
.bottom-bar{left:0;top:2371px;width:1200px;height:35px;background:var(--red);color:#fff;font-size:12px;display:flex;align-items:center}
</style>
</head>
<body>

<!-- top bar -->
<div class="abs quick-btn">
  <svg width="13" height="13" viewBox="0 0 13 13"><rect x="1" y="2" width="11" height="10" fill="none" stroke="#fff" stroke-width="1.5"/><line x1="1" y1="5" x2="12" y2="5" stroke="#fff" stroke-width="1.5"/><line x1="4" y1="0" x2="4" y2="3" stroke="#fff" stroke-width="1.5"/><line x1="9" y1="0" x2="9" y2="3" stroke="#fff" stroke-width="1.5"/></svg>
  QUICK INQUERY
</div>
<div class="abs top-contact" style="left:783px">
  <svg width="16" height="11" viewBox="0 0 16 11"><rect x=".75" y=".75" width="14.5" height="9.5" fill="none" stroke="#1c1aa0" stroke-width="1.5"/><path d="M1 1 L8 6 L15 1" fill="none" stroke="#1c1aa0" stroke-width="1.5"/></svg>
  ouremailaddress@fernmail.net
</div>
<div class="abs top-contact" style="left:1004px">
  <svg width="15" height="15" viewBox="0 0 24 24"><path fill="#1c1aa0" d="M6.6 10.8a15.1 15.1 0 006.6 6.6l2.2-2.2c.3-.3.7-.4 1-.2 1.1.4 2.3.6 3.6.6.6 0 1 .4 1 1V20c0 .6-.4 1-1 1A17 17 0 013 4c0-.6.4-1 1-1h3.5c.6 0 1 .4 1 1 0 1.3.2 2.5.6 3.6.1.3 0 .7-.2 1z"/></svg>
  (206) 555-0148
</div>

<!-- navigation -->
<div class="abs nav-band"></div>
<span class="abs nav-item active" style="left:80px">Home</span>
<span class="abs nav-star" style="left:189px">★</span>
<span class="abs nav-item" style="left:218px">About Us</span>
<span class="abs nav-star" style="left:333px">★</span>
<span class="abs nav-item" style="left:385px">Services</span>
<span class="abs nav-star" style="left:497px">★</span>
<span class="abs nav-star" style="left:694px">★</span>
<span class="abs nav-item" style="left:728px">Prices</span>
<span class="abs nav-star" style="left:810px">★</span>
<span class="abs nav-item" style="left:839px">Photo Gallery</span>
<span class="abs nav-star" style="left:989px">★</span>
<span class="abs nav-item" style="left:1023px">Contact Us</span>
<div class="abs logo-disc">KESTREL<br>WAY</div>

<!-- hero -->
<div class="abs hero" role="img" aria-label="Spa still life with bamboo, towels, candle, daisies and stones beside a couple relaxing during a massage"></div>
<div class="abs hero-title">MASSAGE</div>
<div class="abs hero-sub">THERAPY</div>
<div class="abs hero-tag">We come to you</div>

<!-- about -->
<div class="abs section-title" style="top:688px">ABOUT <span>US</span></div>
<svg class="abs divider" style="top:733px" viewBox="0 0 200 20"><line x1="0" y1="8" x2="84" y2="8" stroke="#d9b2a4"/><line x1="0" y1="12" x2="84" y2="12" stroke="#d9b2a4"/><line x1="116" y1="8" x2="200" y2="8" stroke="#d9b2a4"/><line x1="116" y1="12" x2="200" y2="12" stroke="#d9b2a4"/><circle cx="100" cy="10" r="10" fill="#333"/></svg>
<p class="abs about-lead">We are a male and female mobile massage team. Our names are Paul and Lina. Kestrel Way is a Seattle based mobile massage service. Our massage is offered to the community with a goal of facilitating balance within each individual. We specialize in integrated Pain management, and sports/medical massage therapy. Every client's first assessment is attended by our male and female massage therapist team. Depending on the goals identified for an individual determines which therapist will be assigned to provide treatment, if not both.</p>
<div class="abs about-photo" role="img" aria-label="Pink gerbera flowers with stacked grey spa stones and scattered petals"></div>

<div class="abs feature-icon" style="left:604px;top:858px"><svg width="40" height="40" viewBox="0 0 40 40" fill="none" stroke="#fff" stroke-width="2.5"><circle cx="20" cy="10" r="5"/><path d="M8 28h24M12 28v6M28 28v6M12 22h16"/></svg></div>
<div class="abs feature-title" style="top:856px">Why We Stand Out?</div>
<p class="abs feature-text" style="top:882px">Kestrel Way is a Seattle based mobile massage service. Our massage is offered to the community with a goal of facilitating balance within each individual.</p>
<div class="abs read-more" style="top:933px">Read More <svg width="12" height="10" viewBox="0 0 12 10" fill="none" stroke="#1c1aa0" stroke-width="2"><path d="M1 1l4 4-4 4M6 1l4 4-4 4"/></svg></div>

<div class="abs feature-icon" style="left:604px;top:959px"><svg width="40" height="40" viewBox="0 0 40 40" fill="#fff"><path d="M20 33 L7 20 A7 7 0 0 1 20 11 A7 7 0 0 1 33 20 Z"/></svg></div>
<div class="abs feature-title" style="top:961px">Our Passion.</div>
<p class="abs feature-text" style="top:985px">Here at Kestrel Way, we have a great passion for Postural Resoration and how it is integrated into an individual's Massage treatment. We pride ourselves in being natural</p>
<div class="abs read-more" style="top:1032px">Read More <svg width="12" height="10" viewBox="0 0 12 10" fill="none" stroke="#1c1aa0" stroke-width="2"><path d="M1 1l4 4-4 4M6 1l4 4-4 4"/></svg></div>

<div class="abs feature-icon" style="left:604px;top:1060px"><svg width="40" height="40" viewBox="0 0 40 40" fill="none" stroke="#fff" stroke-width="2.5"><rect x="9" y="8" width="24" height="17"/><path d="M21 25v8M14 33h14"/></svg></div>
<div class="abs feature-title" style="top:1061px">Our Education.</div>
<p class="abs feature-text" style="top:1085px">We are both Graduates of Venmora, school of massage therapy. We have continuing education in medical massage, myofacial release, trigger point therapy, postural restoration, anatomy</p>
<div class="abs read-more" style="top:1133px">Read More <svg width="12" height="10" viewBox="0 0 12 10" fill="none" stroke="#1c1aa0" stroke-width="2"><path d="M1 1l4 4-4 4M6 1l4 4-4 4"/></svg></div>

<!-- prices -->
<div class="abs prices"></div>
<div class="abs section-title" style="top:1214px">OUR <span>PRICES</span></div>
<svg class="abs divider" style="top:1262px" viewBox="0 0 200 20"><line x1="0" y1="8" x2="84" y2="8" stroke="#d9b2a4"/><line x1="0" y1="12" x2="84" y2="12" stroke="#d9b2a4"/><line x1="116" y1="8" x2="200" y2="8" stroke="#d9b2a4"/><line x1="116" y1="12" x2="200" y2="12" stroke="#d9b2a4"/><circle cx="100" cy="10" r="10" fill="#333"/></svg>

<div class="abs price-card" style="left:80px"><div class="head">60 minutes</div><div class="badge">$75</div><div class="name">Massage Therapy</div><p class="desc">Both Lina and I worked as behavioral health professionals that specialized in life skills mentoring for</p><div class="btn">Read More</div></div>
<div class="abs price-card" style="left:346px"><div class="head">90 minutes</div><div class="badge">$95</div><div class="name">Massage Therapy</div><p class="desc">Both Lina and I worked as behavioral health professionals that specialized in life skills mentoring for</p><div class="btn">Read More</div></div>
<div class="abs price-card" style="left:613px"><div class="head">120 minutes</div><div class="badge">$120</div><div class="name">Massage Therapy</div><p class="desc">Both Lina and I worked as behavioral health professionals that specialized in life skills mentoring for</p><div class="btn">Read More</div></div>
<div class="abs price-card" style="left:879px"><div class="head">150 minutes</div><div class="badge">$150</div><div class="name">Massage Therapy</div><p class="desc">Both Lina and I worked as behavioral health professionals that specialized in life skills mentoring for</p><div class="btn">Read More</div></div>

<!-- testimonials -->
<div class="abs section-title" style="top:1749px">CLIENT <span>TESTIMONIALS</span></div>
<svg class="abs divider" style="top:1795px" viewBox="0 0 200 20"><line x1="0" y1="8" x2="84" y2="8" stroke="#d9b2a4"/><line x1="0" y1="12" x2="84" y2="12" stroke="#d9b2a4"/><line x1="116" y1="8" x2="200" y2="8" stroke="#d9b2a4"/><line x1="116" y1="12" x2="200" y2="12" stroke="#d9b2a4"/><circle cx="100" cy="10" r="10" fill="#333"/></svg>
<div class="abs avatar"><div role="img" aria-label="Portrait photo of the client giving the testimonial"></div></div>
<div class="abs spa-left" role="img" aria-label="Rolled lavender towel with spa stones and lavender sprigs"></div>
<div class="abs spa-right" role="img" aria-label="Stacked white towels with green candles and a pink flower"></div>
<div class="abs quote-mark">“</div>
<p class="abs quote-text">The most important thing to 'us', as Licenced providers is to get you on to our table to show you our skills. But a good therapist never forgets that it's not about what we do for you, but what we can facilitate for you.</p>
<div class="abs quote-name">Ms. Dana Wren</div>
<span class="abs dot" style="left:570px"></span>
<span class="abs dot on" style="left:594px"></span>
<span class="abs dot" style="left:618px"></span>

<!-- footer -->
<div class="abs footer"></div>
<div class="abs footer-title" style="left:82px">Quick Links</div>
<div class="abs footer-rule" style="left:82px;width:125px"></div>
<ul class="abs quick-links">
  <li>Home</li><li>About US</li><li>Services</li><li>Prices</li><li>Photo Gallery</li><li>Contact Us</li>
</ul>
<div class="abs footer-sep" style="left:257px"></div>

<div class="abs footer-title" style="left:311px">Quick Inquiry</div>
<div class="abs field" style="top:2199px;height:24px">Name</div>
<div class="abs field" style="top:2228px;height:24px">Email</div>
<div class="abs field" style="top:2258px;height:42px">Message</div>
<div class="abs submit">Submit</div>
<div class="abs footer-sep" style="left:589px"></div>

<div class="abs footer-title" style="left:642px">Contact Details</div>
<div class="abs footer-rule" style="left:642px;width:236px"></div>
<div class="abs contact-row" style="top:2196px">
  <svg width="10" height="14" viewBox="0 0 10 14" style="flex:none;margin-top:3px"><path fill="#fff" d="M5 0a5 5 0 015 5c0 4-5 9-5 9S0 9 0 5a5 5 0 015-5z"/><circle cx="5" cy="5" r="2" fill="#28235f"/></svg>
  <span>Lorem ipsum dolor sit amet, consectetuer adipiscing elit, sed diam nonummy nibh .</span>
</div>
<div class="abs contact-row" style="top:2263px">
  <svg width="13" height="13" viewBox="0 0 24 24" style="flex:none;margin-top:3px"><path fill="#fff" d="M6.6 10.8a15.1 15.1 0 006.6 6.6l2.2-2.2c.3-.3.7-.4 1-.2 1.1.4 2.3.6 3.6.6.6 0 1 .4 1 1V20c0 .6-.4 1-1 1A17 17 0 013 4c0-.6.4-1 1-1h3.5c.6 0 1 .4 1 1 0 1.3.2 2.5.6 3.6.1.3 0 .7-.2 1z"/></svg>
  <span>(206) 555-0148</span>
</div>
<div class="abs contact-row" style="top:2295px">
  <svg width="14" height="10" viewBox="0 0 16 11" style="flex:none;margin-top:5px"><rect x=".75" y=".75" width="14.5" height="9.5" fill="none" stroke="#fff" stroke-width="1.5"/><path d="M1 1 L8 6 L15 1" fill="none" stroke="#fff" stroke-width="1.5"/></svg>
  <span>ouremailaddress@fernmail.net</span>
</div>
<div class="abs footer-sep" style="left:927px"></div>

<div class="abs footer-logo">KESTREL<br>WAY</div>
<span class="abs social" style="left:1003px;background:#1877d6" role="img" aria-label="Social link"></span>
<span class="abs social" style="left:1043px;background:#1d9fe0" role="img" aria-label="Social link"></span>
<span class="abs social" style="left:1083px;background:#d62b2b" role="img" aria-label="Social link"></span>

<div class="abs bottom-bar">
  <span style="position:absolute;left:82px">Copyright © 2015 kestrelwaymassage | All Right Reserved.</span>
  <span style="position:absolute;left:897px">Terms &amp; Conditions</span>
  <span style="position:absolute;left:1021px">|</span>
  <span style="position:absolute;left:1039px">Privacy Policy</span>
</div>

</body>
</html>
```